Graphic Design for a 3 Banner Tradeshow Setup

We are a Pipe Restoration company that specializes in trenchless pipelining. We need a design for a 3 banner setup to use at tradeshows. See attached "banner specs" for sizing - note the 48" x 92" will be in between the two 36" x 92" banners. See attached "Mock-Up" of information each banner needs and utilize the color scheme of the banners we already have in the "both DWM banners" AI file attached. The final designs should communicate what we do and attract people into our booth. We would like to have graphics of realistic pipes for a before (dirty pipe), after cleaning pipe, and lined pipe - see example of "pipe pictures" attached. I'm not sure if this is something you can generate or if we will need to find images of our own to send. Also, see attached "screenshot-process" to see similar images we would like to use to showcase the process.
Target Market(s)
Homeowners, Property Managers, HOA Communities, Healthcare Facilities & Hospitals, and commercial properties
Industry/Entity Type
Trenchless Pipelining
Look and feel

```html
<!DOCTYPE html>
<html lang="en">
<head>
<meta charset="utf-8">
<title>DWM Tradeshow Banners</title>
<link href="https://fonts.googleapis.com/css2?family=Krona+One&family=Poppins:wght@300;400;600;700&display=swap" rel="stylesheet">
<style>
  :root {
    --stage: #939393;
    --navy: #1c2b55;
    --navy-deep: #14203f;
    --band-blue: #1557b0;
    --brand-blue: #1a4fa8;
    --ink: #1b1b1b;
    --cyan: #00b8ec;
    --violet: #2c3385;
    --midnight: #111a33;
    --white: #ffffff;
    --placeholder-grey: #8c9398;
    --placeholder-grey-soft: #a9b0b4;
    --placeholder-blue: #6ccbe6;
    --placeholder-blue-soft: #93d9ec;
  }
  * { box-sizing: border-box; margin: 0; padding: 0; }
  html, body { width: 1200px; height: 878px; overflow: hidden; }
  body { background: var(--stage); position: relative; font-family: "Poppins", sans-serif; }

  .banner { position: absolute; top: 10px; height: 854px; overflow: hidden; }
  .banner--side { width: 334px; background: linear-gradient(160deg, #ffffff 0%, #f1f2f5 60%, #e9ebef 100%); }
  .banner--left { left: 16px; }
  .banner--right { left: 852px; }
  .banner--center { left: 375px; width: 445px; background: linear-gradient(100deg, var(--cyan) 0%, #1a6fc0 45%, var(--violet) 100%); }

  .header-scene { position: absolute; inset: 0 0 auto 0; height: 140px;
    background: linear-gradient(180deg, #22366a 0%, var(--navy) 60%, var(--navy-deep) 100%); }
  .brand { position: absolute; top: 56px; left: 0; right: 0; text-align: center; color: var(--white); }
  .brand-name { font-family: "Krona One", sans-serif; font-size: 40px; line-height: 1; letter-spacing: 6px; display: inline-flex; align-items: center; gap: 10px; }
  .brand-mark { width: 30px; height: 30px; background: var(--cyan); display: inline-block; }
  .brand-tag { font-family: "Krona One", sans-serif; font-size: 8.6px; letter-spacing: 2.6px; margin-top: 6px; }

  .band { position: absolute; top: 140px; left: 0; right: 0; height: 45px; background: var(--band-blue);
    color: var(--white); font-family: "Krona One", sans-serif; font-size: 27px; text-align: center; line-height: 45px; letter-spacing: -0.5px; }

  .service { position: absolute; left: 0; right: 0; text-align: center; }
  .service-icon { width: 44px; height: 44px; display: block; margin: 0 auto; }
  .service-title { font-family: "Krona One", sans-serif; color: var(--brand-blue); font-size: 18.5px; line-height: 1.2; margin-top: 10px; letter-spacing: -0.2px; }
  .service-rule { width: 212px; height: 1.5px; background: var(--brand-blue); margin: 8px auto 0; }

  .contact { position: absolute; left: 0; right: 0; top: 755px; text-align: center; }
  .contact-label { font-size: 15px; color: var(--ink); }
  .contact-phone { margin: 5px 9px 0; height: 33px; background: var(--navy); color: var(--white);
    font-weight: 700; font-size: 27px; line-height: 33px; letter-spacing: 0.5px; }
  .contact-links { display: flex; align-items: center; justify-content: center; gap: 14px; margin-top: 8px; }
  .contact-web { color: var(--brand-blue); font-weight: 600; font-size: 16px; }
  .contact-divider { width: 1px; height: 20px; background: var(--ink); }
  .social { display: flex; gap: 7px; }
  .social span { width: 13px; height: 13px; border-radius: 50%; background: var(--brand-blue); display: block; }

  .problem-list { position: absolute; top: 208px; left: 0; right: 0; text-align: center; list-style: none; }
  .problem-list li { font-family: "Krona One", sans-serif; color: var(--brand-blue); font-size: 19px; line-height: 1.3; margin-bottom: 19px; letter-spacing: -0.2px; }
  .pipe-photo { position: absolute; left: 46px; top: 500px; width: 240px; height: 240px; border-radius: 50%;
    background: linear-gradient(160deg, var(--placeholder-grey-soft) 0%, var(--placeholder-grey) 100%); }

  .headline { position: absolute; left: 0; right: 0; top: 30px; text-align: center; color: var(--white);
    font-family: "Krona One", sans-serif; line-height: 1.18; font-size: 40px; }
  .headline .big { font-size: 45px; letter-spacing: -1px; }
  .lede-band { position: absolute; top: 140px; left: 0; right: 0; height: 123px; background: var(--midnight); }
  .lede { position: absolute; top: 152px; left: 0; right: 0; text-align: center; color: var(--white);
    font-weight: 700; font-size: 20.5px; line-height: 27px; }
  .process-card { position: absolute; top: 224px; left: 19px; width: 404px; height: 610px; background: var(--white); }
  .step-visual { position: absolute; left: 28px; width: 337px; height: 72px; }
  .step-visual--grey { background: linear-gradient(180deg, var(--placeholder-grey-soft) 0%, var(--placeholder-grey) 100%); }
  .step-visual--blue { background: linear-gradient(180deg, var(--placeholder-blue-soft) 0%, var(--placeholder-blue) 100%); }
  .step-num { position: absolute; left: 23px; width: 21px; height: 21px; border-radius: 50%; background: var(--brand-blue);
    color: var(--white); font-size: 12px; font-weight: 600; text-align: center; line-height: 21px; }
  .step-title { position: absolute; right: 39px; font-family: "Krona One", sans-serif; color: var(--brand-blue); font-size: 19px; }
  .step-text { position: absolute; left: 29px; right: 22px; font-size: 10.8px; font-weight: 300; line-height: 16.8px; color: var(--ink); }
</style>
</head>
<body>

<section class="banner banner--side banner--left">
  <div class="header-scene" role="img" aria-label="Photo of a technician reviewing pipe inspection footage"></div>
  <div class="brand">
    <div class="brand-name"><span class="brand-mark"></span>DWM</div>
    <div class="brand-tag">DRAIN WORKS MAINTENANCE</div>
  </div>
  <h2 class="band">WE ASSESS</h2>

  <div class="service" style="top:228px">
    <svg class="service-icon" viewBox="0 0 44 44" fill="none" stroke="#111" stroke-width="1.6">
      <path d="M6 2v30a6 6 0 0 0 6 6h28M10 2v30a2 2 0 0 0 2 2h28"/>
      <rect x="20" y="12" width="18" height="8" rx="2"/><circle cx="29" cy="16" r="2.5"/>
    </svg>
    <div class="service-title">CCTV Pipe Investigation</div>
    <div class="service-rule"></div>
  </div>

  <div class="service" style="top:355px">
    <svg class="service-icon" viewBox="0 0 44 44" fill="none" stroke="#111" stroke-width="1.6">
      <circle cx="18" cy="24" r="12"/><circle cx="18" cy="24" r="6"/><path d="M18 8v32M2 24h32"/>
      <circle cx="32" cy="12" r="6"/><circle cx="32" cy="32" r="5"/>
    </svg>
    <div class="service-title">Scope Development</div>
    <div class="service-rule"></div>
  </div>

  <div class="service" style="top:482px">
    <svg class="service-icon" viewBox="0 0 44 44" fill="none" stroke="#111" stroke-width="1.6">
      <rect x="16" y="4" width="24" height="24" rx="3"/><circle cx="34" cy="16" r="3"/>
      <rect x="4" y="16" width="16" height="24" rx="1"/><path d="M7 20h10M7 26h10M7 31h10M7 36h10M11 24v14M15 24v14"/>
    </svg>
    <div class="service-title">Budgetary Evaluation</div>
    <div class="service-rule"></div>
  </div>

  <div class="service" style="top:609px">
    <svg class="service-icon" viewBox="0 0 44 44" fill="none" stroke="#111" stroke-width="1.6">
      <circle cx="18" cy="18" r="13"/><ellipse cx="18" cy="18" rx="8" ry="5"/><circle cx="18" cy="18" r="2.5"/>
      <path d="M27 27l12 12"/>
    </svg>
    <div class="service-title">Project Oversight</div>
    <div class="service-rule"></div>
  </div>

  <div class="contact">
    <div class="contact-label">Contact Us</div>
    <div class="contact-phone">1-800-555-0142</div>
    <div class="contact-links">
      <span class="contact-web">www.dwmpipe.com</span>
      <span class="contact-divider"></span>
      <span class="social"><span></span><span></span><span></span><span></span></span>
    </div>
  </div>
</section>

<section class="banner banner--center">
  <h1 class="headline"><span>PIPE</span><br><span class="big">PROBLEMS?</span></h1>
  <div class="lede-band"></div>
  <p class="lede">We Help Fix Pipe Problems Without<br>Having To Tear Up Your Buidling</p>

  <div class="process-card">
    <div class="step-visual step-visual--grey" style="top:28px" role="img" aria-label="Illustration of a dirty pipe being cleaned"></div>
    <div class="step-num" style="top:22px">1</div>
    <div class="step-title" style="top:96px">Cleaning</div>
    <p class="step-text" style="top:128px">Blocked, damaged, or root-intruded pipes are cleaned with our hydrojetter or mechanical cleaning tools to get the pipe back to its original shape and diameter</p>

    <div class="step-visual step-visual--grey" style="top:234px" role="img" aria-label="Illustration of a liner being installed inside a pipe"></div>
    <div class="step-num" style="top:233px">2</div>
    <div class="step-title" style="top:302px">Installation</div>
    <p class="step-text" style="top:333px">An epoxy-saturated liner is pulled into place through existing access points such as a toilet or a roof vent and an internal rubber bladder is inflated, pressing the epoxy saturated liner against the existing pipe wall.</p>

    <div class="step-visual step-visual--blue" style="top:439px" role="img" aria-label="Illustration of a restored lined pipe"></div>
    <div class="step-num" style="top:442px">3</div>
    <div class="step-title" style="top:512px">Restored Pipe</div>
    <p class="step-text" style="top:538px">The epoxy cures in a few short hours, then the bladder is deflated and removed, leaving behind a new, clean, and seamless “pipe within a pipe.</p>
  </div>
</section>

<section class="banner banner--side banner--right">
  <div class="header-scene" role="img" aria-label="Photo of a technician reviewing pipe inspection footage"></div>
  <div class="brand">
    <div class="brand-name"><span class="brand-mark"></span>DWM</div>
    <div class="brand-tag">DRAIN WORKS MAINTENANCE</div>
  </div>
  <h2 class="band">WE FIX</h2>

  <ul class="problem-list">
    <li>Slow Drains</li>
    <li>Back-Ups</li>
    <li>Sewer Odors</li>
    <li>Cracked Pipes</li>
    <li>Root Intrusion</li>
    <li>Recurring Plumbing<br>Problems</li>
  </ul>
  <div class="pipe-photo" role="img" aria-label="Photo of a pipe cross-section before and after lining"></div>

  <div class="contact">
    <div class="contact-label">Contact Us</div>
    <div class="contact-phone">1-800-555-0142</div>
    <div class="contact-links">
      <span class="contact-web">www.dwmpipe.com</span>
      <span class="contact-divider"></span>
      <span class="social"><span></span><span></span><span></span><span></span></span>
    </div>
  </div>
</section>

</body>
</html>
```